Modern Business Card

Modern professional business card with more than just logo and demographic info. Something memorable.

We are a trendy/modern chiropractic group with an emphasis on neurology, hence the minimalist-type brain logo. We want to convey that modern and technical aspect with professionalism and the elite nature of our practice environment.

```html
<!DOCTYPE html>
<html lang="en">
<head>
<meta charset="utf-8">
<title>Meridian Chiropractic — Business Card</title>
<link href="https://fonts.googleapis.com/css2?family=Crimson+Pro:wght@400&family=Bitter:wght@400;600&display=swap" rel="stylesheet">
<style>
  :root {
    --backdrop: #2a2a2a;
    --card-white: #ffffff;
    --brand-blue: #4680c4;
    --ink: #1c1c1c;
    --rule: #b9b9b9;
  }
  * { box-sizing: border-box; margin: 0; padding: 0; }
  html, body { width: 1200px; height: 1200px; overflow: hidden; }
  body { background: var(--backdrop); position: relative; font-family: "Bitter", Georgia, serif; }

  .card { position: absolute; top: 310px; height: 594px; }
  .card-front { left: 234px; width: 364px; background: var(--card-white); color: var(--ink); text-align: center; }
  .card-back { left: 627px; width: 369px; background: var(--brand-blue); }

  .brand-dot { position: absolute; left: 159px; top: 86px; width: 46px; height: 46px; border-radius: 50%; background: var(--brand-blue); }

  .wordmark { position: absolute; left: 0; right: 0; font-family: "Crimson Pro", Georgia, serif; font-weight: 400; line-height: 1; }
  .card-front .wordmark { top: 186px; color: var(--ink); }
  .wordmark .line-main { display: block; font-size: 52px; letter-spacing: 1px; }
  .wordmark .line-sub { display: block; font-size: 29px; letter-spacing: 0.5px; margin-top: 2px; }

  .person-name { position: absolute; top: 334px; left: 0; right: 0; font-size: 23px; font-weight: 600; color: var(--brand-blue); letter-spacing: 0.3px; }
  .person-role { position: absolute; top: 362px; left: 0; right: 0; font-size: 16px; }

  .contact-icons { position: absolute; top: 396px; left: 87px; width: 190px; height: 24px; display: flex; align-items: center; gap: 6px; }
  .contact-icons .rule { flex: 1; height: 1px; background: var(--rule); }
  .contact-icons svg { width: 24px; height: 24px; display: block; }

  .contact-lines { position: absolute; top: 432px; left: 0; right: 0; font-size: 15.5px; line-height: 22px; }
  .divider { position: absolute; top: 506px; left: 85px; width: 195px; height: 1px; background: var(--rule); }
  .address { position: absolute; top: 518px; left: 0; right: 0; font-size: 15.5px; line-height: 22px; }

  .card-back .wordmark { top: 452px; left: 62px; right: auto; color: var(--card-white); }
  .card-back .line-main { font-size: 60px; }
  .card-back .line-sub { font-size: 31px; margin-top: -2px; }
</style>
</head>
<body>
  <section class="card card-front">
    <span class="brand-dot"></span>
    <div class="wordmark">
      <span class="line-main">MERIDIAN</span>
      <span class="line-sub">CHIROPRACTIC</span>
    </div>
    <p class="person-name">DANIEL REYES</p>
    <p class="person-role">Managing Director</p>
    <div class="contact-icons">
      <span class="rule"></span>
      <svg viewBox="0 0 24 24" aria-label="Phone"><rect width="24" height="24" rx="3" fill="var(--brand-blue)"/><path d="M5 10c0-3 14-3 14 0v1h-3v-1.5h-8V11H5z M7 12h10l1 6H6z" fill="#fff"/><circle cx="12" cy="15" r="1.6" fill="var(--brand-blue)"/></svg>
      <svg viewBox="0 0 24 24" aria-label="Email"><rect width="24" height="24" rx="3" fill="var(--brand-blue)"/><rect x="5" y="7" width="14" height="10" fill="none" stroke="#fff" stroke-width="1.5"/><path d="M5 7l7 6 7-6" fill="none" stroke="#fff" stroke-width="1.5"/></svg>
      <svg viewBox="0 0 24 24" aria-label="Website"><rect width="24" height="24" rx="3" fill="var(--brand-blue)"/><circle cx="12" cy="12" r="7" fill="#fff"/><path d="M8 9c2 0 3 1 3 3s-2 2-2 4M14 6c0 2 2 3 4 3M15 14c1 1 1 3 0 4" fill="none" stroke="var(--brand-blue)" stroke-width="1.4"/></svg>
      <span class="rule"></span>
    </div>
    <div class="contact-lines">
      <p>044-555 210 348</p>
      <p>hello@meridian.com</p>
      <p>www.meridianspine.com</p>
    </div>
    <span class="divider"></span>
    <div class="address">
      <p>218, Harbour Lane West,</p>
      <p>40917, Northvale</p>
    </div>
  </section>

  <section class="card card-back">
    <div class="wordmark">
      <span class="line-main">MERIDIAN</span>
      <span class="line-sub">CHIROPRACTIC</span>
    </div>
  </section>
</body>
</html>
```